RW Framewell Inc Business cards

We need business cards using our existing logo but slightly modified. Right now the logo says RW Loadbearing Masonry. We want to keep the RW part of the design, but replace the Structural Concrete portion with "FRAMEWELL". Please see the attached file.
Ideally this would be a blank template so we can add Different Names, titles, and phone numbers later.
On the one side we want only the logo and on the other side the detail. I'm attaching an example for you to see.
Please reach out with any other questions. Our address and other details will be given out once we find a design we like.

Target Market(s)

Construction Industry

```html
<!DOCTYPE html>
<html lang="en">
<head>
<meta charset="UTF-8">
<title>RW Framewell Inc – Business Cards</title>
<link href="https://fonts.googleapis.com/css2?family=Roboto:wght@400;500;700&display=swap" rel="stylesheet">
<style>
  :root {
    --backdrop: #3b3b3d;
    --card: #1e1e20;
    --brand-blue: #2f63a8;
    --steel-grey: #8a8a8c;
    --silver: #a9a9ab;
    --text-light: #f2f2f2;
    --icon-grey: #9a9a9c;
  }
  * { margin: 0; padding: 0; box-sizing: border-box; }
  html, body {
    width: 799px;
    height: 1200px;
    overflow: hidden;
    background: var(--backdrop);
    font-family: "Roboto", Arial, sans-serif;
  }
  .sheet {
    position: relative;
    width: 799px;
    height: 1200px;
  }
  .card {
    position: absolute;
    left: 90px;
    width: 620px;
    height: 354px;
    background: var(--card);
    border-radius: 4px;
    overflow: hidden;
    box-shadow: 0 10px 24px rgba(0,0,0,0.45);
  }
  .card--front { top: 130px; }
  .card--back  { top: 716px; }

  /* Front: logo only */
  .wordmark {
    position: absolute;
    font-weight: 700;
    letter-spacing: 0.12em;
    white-space: nowrap;
  }
  .card--front .wordmark {
    left: 0;
    right: 0;
    top: 150px;
    text-align: center;
    font-size: 40px;
    color: var(--silver);
  }

  /* Back: details */
  .card--back .wordmark {
    left: 36px;
    top: 96px;
    font-size: 28px;
    color: var(--text-light);
  }
  .accent-strip {
    position: absolute;
    left: 0;
    top: 262px;
    width: 300px;
    height: 14px;
    background: var(--steel-grey);
  }
  .tagline-band {
    position: absolute;
    left: 270px;
    right: 0;
    bottom: 0;
    height: 78px;
    background: var(--brand-blue);
    border-top-left-radius: 26px;
    display: flex;
    align-items: flex-end;
    justify-content: flex-end;
    padding: 0 26px 16px 0;
  }
  .tagline {
    color: #ffffff;
    font-weight: 700;
    font-size: 18px;
  }
  .contact {
    position: absolute;
    left: 320px;
    top: 58px;
    color: var(--text-light);
  }
  .contact__name {
    font-size: 25px;
    font-weight: 500;
    color: var(--brand-blue);
    line-height: 1.1;
  }
  .contact__title {
    font-size: 14px;
    margin-top: 3px;
    margin-bottom: 14px;
  }
  .contact__list { list-style: none; }
  .contact__item {
    display: flex;
    align-items: center;
    gap: 10px;
    font-size: 16px;
    line-height: 24px;
  }
  .contact__item svg { width: 13px; height: 13px; fill: var(--icon-grey); flex: none; }
  .contact__address {
    font-size: 16px;
    line-height: 22px;
    margin-top: 4px;
  }
</style>
</head>
<body>
<main class="sheet">

  <section class="card card--front" aria-label="Card front">
    <div class="wordmark">RW FRAMEWELL</div>
  </section>

  <section class="card card--back" aria-label="Card back">
    <div class="wordmark">RW FRAMEWELL</div>

    <div class="contact">
      <div class="contact__name">Alex RW Morgan</div>
      <div class="contact__title">Managing Director</div>
      <ul class="contact__list">
        <li class="contact__item">
          <svg viewBox="0 0 16 16" aria-hidden="true"><path d="M3.6 1.2l2.4 2.6-1.3 1.8c.9 2 2.6 3.7 4.6 4.6l1.8-1.3 2.6 2.4-1.5 2.3C6.6 13.5 2.5 9.4 1.4 3z"/></svg>
          <span>555-010-2040</span>
        </li>
        <li class="contact__item">
          <svg viewBox="0 0 16 16" aria-hidden="true"><path d="M1 3h14v10H1z M1.8 3.6L8 8.6l6.2-5" fill-rule="evenodd"/><path d="M1.5 3.5L8 8.8l6.5-5.3" stroke="#1e1e20" stroke-width="1.2" fill="none"/></svg>
          <span>alex@rwframewell.com</span>
        </li>
        <li class="contact__item">
          <svg viewBox="0 0 16 16" aria-hidden="true"><circle cx="8" cy="8" r="7"/><path d="M1 8h14M8 1c-3 3-3 11 0 14M8 1c3 3 3 11 0 14" stroke="#1e1e20" stroke-width="1" fill="none"/></svg>
          <span>www.rwframewell.com</span>
        </li>
      </ul>
      <div class="contact__address">48 Sample Road, Fairview,<br>Oregon, US 970001</div>
    </div>

    <div class="accent-strip"></div>
    <div class="tagline-band">
      <span class="tagline">RW Loadbearing Masonry</span>
    </div>
  </section>

</main>
</body>
</html>
```